CORAL COVE LAUNDROMAT

I NEED A SIGN FOR A NEW LAUNDROMAT THAT I HAVE BUILT
IN THE CITY OF DARWIN BESIDE MY CURRENT HOTEL I OWN
THIS IS A SEMI STAND ALONE BUSNIESS
DARWIN IS A LAID BACK CITY IN AUSTRALIA WERE THING ARE A BIT CHEEKY THE SIGN /LOGO ECT WILL BE APPRO 2 METERS TALL BY 6 METERS LONG ,6 FOOT BY 18 FOOT
sign viewing point is 5 meters to 100 meters

i have put a logo up of my current hotel as a guide it docent have to mach it just food for thought idea

building colour is white and black

like it to be fun or a little sexy risky

```html
<!DOCTYPE html>
<html lang="en">
<head>
<meta charset="utf-8">
<title>Coral Cove Laundromat — Sign</title>
<link rel="stylesheet" href="https://fonts.googleapis.com/css2?family=Montserrat:wght@800&display=swap">
<style>
  :root {
    --canvas-bg: #f1f2f2;
    --banner-top: #ffffff;
    --banner-mid: #e6f1fa;
    --banner-low: #bcd9f0;
    --banner-edge: #d6dde3;
    --wave-light: #cfe4f5;
    --wave-deep: #9cc6ea;
    --brand-blue: #0d519f;
    --ink-dark: #2f3133;
    --halo: #ffffff;
    --figure-light: #eaf3f8;
    --figure-mid: #d3e7ef;
  }
  html, body {
    margin: 0;
    padding: 0;
    width: 1200px;
    height: 599px;
    overflow: hidden;
    background: var(--canvas-bg);
  }
  .sign {
    display: block;
    width: 1200px;
    height: 599px;
  }
  .banner-edge { fill: none; stroke: var(--banner-edge); stroke-width: 1; }
  .wave-soft { fill: var(--wave-light); opacity: 0.7; }
  .wave-deep { fill: var(--wave-deep); opacity: 0.45; }
  .place-name {
    font-family: "Montserrat", sans-serif;
    font-weight: 800;
    font-size: 30px;
    letter-spacing: 17px;
    fill: var(--ink-dark);
  }
  .business-name {
    font-family: "Montserrat", sans-serif;
    font-weight: 800;
    font-size: 120px;
    fill: var(--brand-blue);
    stroke: var(--halo);
    stroke-width: 8px;
    stroke-linejoin: round;
    paint-order: stroke fill;
  }
</style>
</head>
<body>
<svg class="sign" viewBox="0 0 1200 599" xmlns="http://www.w3.org/2000/svg" aria-labelledby="sign-title">
  <title id="sign-title">Coral Cove Laundromat sign</title>
  <defs>
    <radialGradient id="backdrop-glow" cx="50%" cy="45%" r="70%">
      <stop offset="0" stop-color="#fafafa"/>
      <stop offset="1" stop-color="#e9eaeb"/>
    </radialGradient>
    <linearGradient id="banner-fill" x1="0" y1="0" x2="0" y2="1">
      <stop offset="0" stop-color="var(--banner-top)"/>
      <stop offset="0.45" stop-color="var(--banner-mid)"/>
      <stop offset="0.7" stop-color="var(--banner-low)"/>
      <stop offset="1" stop-color="var(--banner-top)"/>
    </linearGradient>
    <linearGradient id="figure-fill" x1="0" y1="0" x2="0" y2="1">
      <stop offset="0" stop-color="var(--figure-light)"/>
      <stop offset="1" stop-color="var(--figure-mid)"/>
    </linearGradient>
    <clipPath id="banner-clip">
      <rect x="25" y="253" width="1150" height="205"/>
    </clipPath>
  </defs>

  <rect width="1200" height="599" fill="url(#backdrop-glow)"/>

  <g class="banner">
    <rect x="25" y="253" width="1150" height="205" fill="url(#banner-fill)"/>
    <g clip-path="url(#banner-clip)">
      <path class="wave-soft" d="M25 380 C 220 330, 420 420, 640 370 S 1000 340, 1175 375 L1175 458 L25 458 Z"/>
      <path class="wave-deep" d="M25 405 C 260 370, 470 440, 700 400 S 1020 385, 1175 410 L1175 430 C 1000 410, 820 440, 640 430 S 260 400, 25 430 Z"/>
    </g>
    <rect class="banner-edge" x="25.5" y="253.5" width="1149" height="204"/>
  </g>

  <rect x="732" y="75" width="240" height="375" rx="18" fill="url(#figure-fill)"
        role="img" aria-label="Illustrated woman in a crop top and mint leggings sitting on a front-loading washing machine"/>

  <text class="place-name" x="45" y="304">CORAL</text>
  <text class="business-name" x="42" y="403" textLength="1108" lengthAdjust="spacingAndGlyphs">COVE LAUNDROMAT</text>
</svg>
</body>
</html>
```